LIFE CHANGING NEW WEBSITE DESIGN NEEDED FOR FULL WEBSITE- FUN/FEMININE!

I need a website designed for a personal financial advice website geared at women called BLUE OTTER LANTERN. I will be providing free financial advice around topics of making, saving, spending and sharing money. The concept is to change the way women understand money and the necessity around building various passive income streams to ensure full financial freedom. This will then carry down to advice for mothers with children and children in particular. The website should be elegant and yet witty. I don't want lots of serious photos but more relatable. I will have a photo of myself and my story as this is a blog and needs to be relatable to women and mothers. I like pinks and greys. I want to have a pink piggy bank being broken with a hammer in the front screen to break our traditional mindset around piggy bank saving/spending habits. I have created a logo that is a pink piggy head with BLUE OTTER LANTERN that needs to be incorporated so that it blends into the heading. I have also already started designing the website on Squarespace and can provide access to that. Basically it should have a format of BLUE OTTER LANTERN LOGO center in header then on left hand navigation: MAKE, SAVE, SPEND, SHARE then on right hand header navigation: MISSION, GET STARTED, CONTACT BOL I would like to have the front page when you go to the url to have the image of the piggy bank being broken then a catchy phrase then under 4 boxes with MAKE (image and description) SAVE (image and description) SPEND (image and description) SHARE (image and description) if you click on those or the title they go to pages that are dedicated to each them. Each page should have a little intro on the topic then I want lots of blog links as I will be mainly writing blogs. Each blog site should have ability to write comments as well. I need social media icons on each page too. Please let me know what you need from me to get started. I prefer having a discussion if possible to not waste anyone's time. I need the site to be easy for me to use and add blogs/urls etc as needed. I also need the site to be put into my domain that I already purchased: www.blueotterlantern-sample.com

Target Market(s)

teenage girls, 20 something girls, 30 something girls and mothers

Coding

Coded - Design and coding required

Number of Pages Required

5+ page

Font styles to use
Sans Serif

Colors
e667a6
e34197
f59195
eea4c8
aaaaaa
cbcbcb
959595

Requirements
Must have
• TOP NAVIGATION
• MAKE SAVE SPEND SHARE LOGO/BLUE OTTER LANTERN MISSION GET STARTED CONTACT BOL
• FRONT PAGE: IMAGE OF PIGGY BANK BEING BROKEN WITH A HAMMER
• CATCH PHRASE OVER THE IMAGE
• BUTTON IN PINK- TAKE ACTION (WHICH DIRECTS TO TAKE ACTION TAB ON NAVIGATION HEADER
• 4 BOXES BELOW MAIN IMAGE WITH IMAGE/DESCRIPTIONS FOR MAKE, SAVE, SPEND, SHARE THAT EACH GO TO THE PAGES FROM THE NAVIGATION HEADER
• EACH PAGE SHOULD BE DEDICATED TO THOSE TOPICS THEN THERE IS AN INTRO ON EACH PAGE THEN THE LINKS TO DIFFERENT BLOGS AROUND EACH TOPIC FOR MAKE, SAVE, SPEND, SHARE
• EACH BLOG SHOULD HAVE COMMENTS SECTION AND SOCIAL MEDIA ICONS
• (GOOD TO USE PINKS/GREYS)
Should not have
• BE SUPER BUSY, CLUTTERED, FEEL LIKE I AM SELLING SOMETHING

```html
<!DOCTYPE html>
<html lang="en">
<head>
<meta charset="utf-8">
<title>Blue Otter Lantern – Free Financial Advice</title>
<link href="https://fonts.googleapis.com/css2?family=Poppins:wght@400;500;600;700&family=Open+Sans:wght@400;600&display=swap" rel="stylesheet">
<style>
:root{
  --pink:#e34197;
  --pink-soft:#e667a6;
  --pink-pale:#eea4c8;
  --coral:#f59195;
  --grey-light:#cbcbcb;
  --grey:#aaaaaa;
  --grey-dark:#959595;
  --ink:#2b2b2b;
  --text:#555555;
  --band:#f2f2f2;
  --footer:#232323;
  --white:#ffffff;
}
*{box-sizing:border-box;margin:0;padding:0}
html,body{width:1200px;height:3004px;overflow:hidden}
body{font-family:"Open Sans",sans-serif;color:var(--text);background:var(--white);position:relative}
h1,h2,h3,h4,.nav a,.btn,.brand{font-family:"Poppins",sans-serif}

/* header */
.site-header{height:128px;display:flex;align-items:center;justify-content:space-between;padding:0 40px;background:var(--white)}
.nav{display:flex;gap:34px}
.nav a{font-size:17px;font-weight:600;color:var(--ink);text-decoration:none;letter-spacing:.5px}
.brand{display:flex;align-items:center;gap:12px;color:var(--pink);font-weight:600;font-size:30px;text-decoration:none}
.brand-dot{width:40px;height:40px;border-radius:50%;background:var(--pink-pale)}

/* hero */
.hero{position:relative;height:552px;background:linear-gradient(100deg,#e7e7e7 0%,#bdbdbd 45%,#8a8a8a 80%,#6f6f6f 100%)}
.hero-photo{position:absolute;inset:0;background:radial-gradient(ellipse 260px 180px at 700px 380px,rgba(238,164,200,.85),rgba(238,164,200,0) 70%)}
.hero-content{position:absolute;left:60px;top:110px}
.hero h1{font-size:66px;line-height:78px;font-weight:700;color:var(--white);max-width:560px}
.btn{display:inline-block;background:var(--pink);color:var(--white);font-weight:600;text-decoration:none;text-transform:uppercase}
.hero .btn{margin-top:36px;font-size:20px;padding:18px 36px}
.slider-arrow{position:absolute;top:260px;width:34px;height:40px;background:rgba(30,30,30,.75);display:flex;align-items:center;justify-content:center}
.slider-arrow.prev{left:0}.slider-arrow.next{right:0}

/* pillars */
.pillars{height:384px;margin-top:8px;background:var(--grey-light);display:flex;justify-content:space-between;padding:20px 22px 0}
.pillar{width:270px;height:344px;background:var(--white);position:relative}
.pillar-photo{height:200px}
.pillar-icon{position:absolute;left:20px;top:176px;width:48px;height:48px;border-radius:50%;background:var(--pink);display:flex;align-items:center;justify-content:center}
.pillar h3{margin:34px 20px 6px;font-size:17px;font-weight:600;color:var(--ink)}
.pillar p{margin:0 20px;font-size:13px;line-height:19px}
.pillar .btn{margin:14px 20px 0;font-size:12px;padding:7px 14px}

/* about */
.about{position:relative;height:480px;margin-top:48px}
.about-photo{position:absolute;left:132px;top:40px;width:448px;height:400px;background:linear-gradient(160deg,#f4f4f4,#d9d9d9 60%,#bfbfbf)}
.about-text{position:absolute;left:660px;top:44px;width:420px;padding-left:24px;border-left:5px solid var(--pink)}
.about-text h4{font-size:17px;font-weight:500;color:var(--ink);letter-spacing:.5px}
.about-text h2{font-size:26px;font-weight:700;color:var(--ink);margin-bottom:22px}
.about-text p{font-size:15px;line-height:24px;margin-bottom:18px}
.about-text .btn{font-size:14px;padding:10px 20px;margin-top:4px}

/* blog */
.blog{position:relative;height:580px;margin-top:80px;background:var(--band);padding:68px 128px 0}
.blog-head{display:flex;justify-content:space-between;align-items:center;margin-bottom:32px}
.blog-head h2{font-size:34px;font-weight:700;color:var(--ink)}
.blog-arrows{display:flex;gap:22px}
.blog-grid{display:flex;gap:20px;margin-left:4px}
.post{width:300px;background:var(--white);box-shadow:0 2px 8px rgba(0,0,0,.08)}
.post-photo{height:200px}
.post-body{padding:20px 20px 16px}
.post h3{font-size:16px;line-height:22px;font-weight:700;color:var(--ink);margin-bottom:10px}
.post p{font-size:13px;line-height:19px}
.post .btn{margin-top:14px;font-size:12px;padding:6px 12px}
.post-foot{border-top:1px solid #e6e6e6;padding:12px 20px;display:flex;justify-content:space-between;align-items:center;font-size:13px}
.post-foot .comments{display:flex;align-items:center;gap:8px}
.share{display:flex;gap:8px}
.share span{width:12px;height:12px;border-radius:50%;background:var(--grey-dark)}

/* testimonial */
.testimonial{position:absolute;left:128px;top:2288px;width:944px;height:320px;background:linear-gradient(135deg,var(--pink-soft),var(--pink) 55%,#c9307f)}
.testimonial .author{position:absolute;left:50%;top:34px;transform:translateX(-50%);background:var(--pink-soft);color:var(--white);font-family:"Poppins",sans-serif;font-weight:600;font-size:14px;padding:6px 22px;letter-spacing:.5px}
.testimonial blockquote{position:absolute;left:90px;right:90px;top:100px;text-align:center;color:var(--white);font-size:24px;line-height:36px}
.quote-mark{position:absolute;color:var(--white);font-family:"Poppins",sans-serif;font-size:90px;font-weight:700;line-height:1}
.quote-mark.open{left:40px;top:80px}.quote-mark.close{right:40px;top:200px}
.dots{position:absolute;left:50%;bottom:26px;transform:translateX(-50%);display:flex;gap:10px}
.dots span{width:10px;height:10px;border-radius:50%;background:var(--pink-pale)}
.dots span.active{background:var(--white)}

/* footer */
.site-footer{position:absolute;left:0;top:2648px;width:1200px;height:356px;background:var(--footer);color:#d0d0d0}
.footer-brand{position:absolute;left:128px;top:110px;font-size:28px}
.footer-col{position:absolute;top:56px}
.footer-col h4{font-size:14px;font-weight:600;color:var(--white);margin-bottom:20px;letter-spacing:.5px}
.footer-col li{list-style:none;display:flex;align-items:flex-start;gap:12px;font-size:13px;line-height:19px;margin-bottom:16px}
.footer-col.contact{left:488px;width:260px}
.footer-col.connect{left:860px}
.social-dot{width:22px;height:22px;border-radius:50%;background:var(--pink);flex:none}
.copyright{position:absolute;left:0;right:0;bottom:26px;text-align:center;font-size:12px;color:var(--grey)}
</style>
</head>
<body>

<header class="site-header">
  <nav class="nav">
    <a href="#">MAKE</a><a href="#">SAVE</a><a href="#">SPEND</a><a href="#">SHARE</a>
  </nav>
  <a class="brand" href="#"><span class="brand-dot"></span>Blue Otter Lantern</a>
  <nav class="nav">
    <a href="#">MISSION</a><a href="#">GET STARTED</a><a href="#">CONTACT BOL</a>
  </nav>
</header>

<section class="hero">
  <div class="hero-photo" role="img" aria-label="Photo of a hammer striking a pink piggy bank on a grey background"></div>
  <div class="hero-content">
    <h1>FREE FINANCIAL ADVICE</h1>
    <a class="btn" href="#">Take Action</a>
  </div>
  <span class="slider-arrow prev"><svg width="12" height="16" viewBox="0 0 12 16"><path d="M9 2 3 8l6 6" fill="none" stroke="#fff" stroke-width="2"/></svg></span>
  <span class="slider-arrow next"><svg width="12" height="16" viewBox="0 0 12 16"><path d="m3 2 6 6-6 6" fill="none" stroke="#fff" stroke-width="2"/></svg></span>
</section>

<section class="pillars">
  <article class="pillar">
    <div class="pillar-photo" role="img" aria-label="Photo of a woman working at a desk" style="background:linear-gradient(135deg,#e9d6cf,#b9a59c)"></div>
    <span class="pillar-icon"><svg width="22" height="22" viewBox="0 0 22 22"><rect x="3" y="7" width="16" height="11" rx="2" fill="none" stroke="#fff" stroke-width="2"/><path d="M8 7V4h6v3" fill="none" stroke="#fff" stroke-width="2"/></svg></span>
    <h3>MAKE</h3>
    <p>Lorem Ipsum is simply dummy text of the printing.</p>
    <a class="btn" href="#">Read More</a>
  </article>
  <article class="pillar">
    <div class="pillar-photo" role="img" aria-label="Photo of a pink piggy bank with coins" style="background:linear-gradient(135deg,#d8d8d8,#f2c3d9 55%,#a9a9a9)"></div>
    <span class="pillar-icon"><svg width="22" height="22" viewBox="0 0 22 22"><circle cx="11" cy="12" r="7" fill="none" stroke="#fff" stroke-width="2"/><path d="M11 8v8M8.5 10h4a1.5 1.5 0 0 1 0 3h-3a1.5 1.5 0 0 0 0 3h4" fill="none" stroke="#fff" stroke-width="1.5"/></svg></span>
    <h3>SAVE</h3>
    <p>Lorem Ipsum is simply dummy text of the printing.</p>
    <a class="btn" href="#">Read More</a>
  </article>
  <article class="pillar">
    <div class="pillar-photo" role="img" aria-label="Photo of a fan of banknotes held in hands" style="background:linear-gradient(135deg,#cfd6c7,#8e9a83)"></div>
    <span class="pillar-icon"><svg width="22" height="22" viewBox="0 0 22 22"><path d="M3 5h3l2 10h10l2-7H7" fill="none" stroke="#fff" stroke-width="2"/><circle cx="9" cy="18" r="1.5" fill="#fff"/><circle cx="17" cy="18" r="1.5" fill="#fff"/></svg></span>
    <h3>SPEND</h3>
    <p>Lorem Ipsum is simply dummy text of the printing.</p>
    <a class="btn" href="#">Read More</a>
  </article>
  <article class="pillar">
    <div class="pillar-photo" role="img" aria-label="Photo of a hand holding a phone with network connections" style="background:linear-gradient(135deg,#2c3550,#5a6a9a)"></div>
    <span class="pillar-icon"><svg width="22" height="22" viewBox="0 0 22 22"><circle cx="6" cy="11" r="2.5" fill="#fff"/><circle cx="16" cy="5" r="2.5" fill="#fff"/><circle cx="16" cy="17" r="2.5" fill="#fff"/><path d="m6 11 10-6M6 11l10 6" stroke="#fff" stroke-width="1.6"/></svg></span>
    <h3>SHARE</h3>
    <p>Lorem Ipsum is simply dummy text of the printing.</p>
    <a class="btn" href="#">Read More</a>
  </article>
</section>

<section class="about">
  <div class="about-photo" role="img" aria-label="Photo of the author working at a laptop in a bright office"></div>
  <div class="about-text">
    <h4>WELCOME TO</h4>
    <h2>BLUE OTTER LANTERN</h2>
    <p>My mission is simple: I want to challenge you to rethink the way you think about growing, spending and saving money. By redesigning your life around your finances I want you to run your life as if you are the CEO of your own business, and the business is maximising the value and profitability of your life.</p>
    <p>It is shocking that in today's world of information we are still living in a society where most educated people leave school without even a basic understanding of money and how to run their lives outside of just obtaining a job.</p>
    <a class="btn" href="#">Read More</a>
  </div>
</section>

<section class="blog">
  <div class="blog-head">
    <h2>LATEST BLOG</h2>
    <div class="blog-arrows">
      <svg width="12" height="18" viewBox="0 0 12 18"><path d="M10 2 3 9l7 7" fill="none" stroke="#959595" stroke-width="2"/></svg>
      <svg width="12" height="18" viewBox="0 0 12 18"><path d="m2 2 7 7-7 7" fill="none" stroke="#2b2b2b" stroke-width="2"/></svg>
    </div>
  </div>
  <div class="blog-grid">
    <article class="post">
      <div class="post-photo" role="img" aria-label="Photo of a hammer above a pink piggy bank" style="background:linear-gradient(160deg,#e6e6e6,#f0b9d3 60%,#c9c9c9)"></div>
      <div class="post-body">
        <h3>LOREM IPSUM IS SIMPLY DUMMY TEXT OF...</h3>
        <p>Lorem ipsum dolor sit amet, consectetur adipiscing elit, sed do eiusmod tempor.</p>
        <a class="btn" href="#">Read More</a>
      </div>
      <div class="post-foot"><span class="comments"><svg width="16" height="14" viewBox="0 0 16 14"><path d="M1 1h14v9H6l-4 3v-3H1z" fill="#959595"/></svg>Comment</span><span class="share"><span></span><span></span><span></span></span></div>
    </article>
    <article class="post">
      <div class="post-photo" role="img" aria-label="Photo of a woman smiling at a laptop" style="background:linear-gradient(160deg,#d9dee3,#9fa8b0)"></div>
      <div class="post-body">
        <h3>LOREM IPSUM IS SIMPLY DUMMY TEXT OF...</h3>
        <p>Lorem ipsum dolor sit amet, consectetur adipiscing elit, sed do eiusmod tempor.</p>
        <a class="btn" href="#">Read More</a>
      </div>
      <div class="post-foot"><span class="comments"><svg width="16" height="14" viewBox="0 0 16 14"><path d="M1 1h14v9H6l-4 3v-3H1z" fill="#959595"/></svg>Comment</span><span class="share"><span></span><span></span><span></span></span></div>
    </article>
    <article class="post">
      <div class="post-photo" role="img" aria-label="Photo of a woman in a bright office" style="background:linear-gradient(160deg,#f1ede6,#c8bfae)"></div>
      <div class="post-body">
        <h3>LOREM IPSUM IS SIMPLY DUMMY TEXT OF...</h3>
        <p>Lorem ipsum dolor sit amet, consectetur adipiscing elit, sed do eiusmod tempor.</p>
        <a class="btn" href="#">Read More</a>
      </div>
      <div class="post-foot"><span class="comments"><svg width="16" height="14" viewBox="0 0 16 14"><path d="M1 1h14v9H6l-4 3v-3H1z" fill="#959595"/></svg>Comment</span><span class="share"><span></span><span></span><span></span></span></div>
    </article>
  </div>
</section>

<section class="testimonial">
  <span class="author">NADIA FERNLEY</span>
  <span class="quote-mark open">“</span>
  <blockquote>Sed ut perspiciatis unde omnis iste natus error sit voluptatem accusantium doloremque laudantium totam rem aperiam eaque ipsa quae ab illo inventore veritatis et quasi architecto.</blockquote>
  <span class="quote-mark close">”</span>
  <div class="dots"><span></span><span class="active"></span><span></span><span></span></div>
</section>

<footer class="site-footer">
  <a class="brand footer-brand" href="#"><span class="brand-dot"></span>Blue Otter Lantern</a>
  <div class="footer-col contact">
    <h4>CONTACT US</h4>
    <ul>
      <li><svg width="14" height="18" viewBox="0 0 14 18"><path d="M7 1a6 6 0 0 0-6 6c0 4.5 6 10 6 10s6-5.5 6-10a6 6 0 0 0-6-6z" fill="#e34197"/><circle cx="7" cy="7" r="2" fill="#232323"/></svg>1428 Maple Orchard Lane,<br>Fairview, 20481</li>
      <li><svg width="14" height="16" viewBox="0 0 14 16"><path d="M3 1h3l1 4-2 1a8 8 0 0 0 4 4l1-2 4 1v3c0 1-1 2-2 2A12 12 0 0 1 1 3c0-1 1-2 2-2z" fill="#e34197"/></svg>555-0134-2290</li>
      <li><svg width="16" height="12" viewBox="0 0 16 12"><rect x="0.5" y="0.5" width="15" height="11" fill="none" stroke="#e34197"/><path d="m1 1 7 6 7-6" fill="none" stroke="#e34197"/></svg>hello@blueotterlantern-sample.com</li>
    </ul>
  </div>
  <div class="footer-col connect">
    <h4>CONNECT WITH US</h4>
    <ul>
      <li><span class="social-dot"></span>Pagestream</li>
      <li><span class="social-dot"></span>Chirpline</li>
      <li><span class="social-dot"></span>Worknet</li>
    </ul>
  </div>
  <p class="copyright">Copyright © 2019 All Rights Reserved · www.blueotterlantern-sample.com</p>
</footer>

</body>
</html>
```